Oil and Gas Exploration and Production company needs a business card design

We need a business card design using our logo and colors in the logo. We want a mainstream design.

```html
<!DOCTYPE html>
<html lang="en">
<head>
<meta charset="utf-8">
<title>Arcadia Oil &amp; Gas – Business Card</title>
<link rel="stylesheet" href="https://fonts.googleapis.com/css2?family=Roboto+Slab:wght@800&family=Arimo:wght@400;700&display=swap">
<style>
  :root {
    --ink: #111111;
    --ink-soft: #2a2a2a;
    --paper: #ffffff;
    --gold: #d4ad3b;
    --backdrop: #d8cfc3;
  }
  * { margin: 0; padding: 0; box-sizing: border-box; }
  html, body { width: 1200px; height: 780px; overflow: hidden; }
  body {
    background: var(--backdrop);
    font-family: "Arimo", Arial, sans-serif;
    position: relative;
  }
  .card {
    position: absolute;
    top: 235px;
    width: 540px;
    height: 309px;
    overflow: hidden;
    box-shadow: 0 10px 28px rgba(0,0,0,.25);
  }
  .card--front { left: 40px; background: var(--ink); }
  .card--back { left: 620px; background: var(--paper); }
  .card__shape { position: absolute; inset: 0; width: 100%; height: 100%; }

  .brand {
    position: absolute;
    display: flex;
    align-items: center;
    gap: 10px;
    font-family: "Roboto Slab", Georgia, serif;
    font-weight: 800;
    color: var(--ink);
    white-space: nowrap;
  }
  .brand__dot { border-radius: 50%; background: var(--gold); flex: none; }
  .card--front .brand { left: 250px; top: 26px; font-size: 30px; line-height: 1; }
  .card--front .brand__dot { width: 22px; height: 22px; }
  .card--back .brand { right: 34px; top: 70px; font-size: 50px; line-height: 1; flex-direction: column; align-items: flex-end; gap: 4px; }
  .brand__sub { font-size: 26px; }

  .social { position: absolute; right: 26px; top: 104px; display: flex; gap: 8px; }
  .social__dot { width: 24px; height: 24px; border-radius: 50%; background: var(--paper); }

  .person { position: absolute; left: 32px; top: 186px; }
  .person__name { color: var(--paper); font-weight: 700; font-size: 20px; }
  .person__role { color: var(--gold); font-size: 14px; margin-top: 3px; }

  .contact {
    position: absolute; left: 230px; top: 184px;
    color: var(--paper); font-size: 13px; line-height: 1.45;
    list-style: none;
  }
  .contact__row { display: flex; align-items: center; gap: 6px; }
  .contact__icon { width: 14px; height: 14px; flex: none; }
  .contact__address { padding-left: 20px; }
</style>
</head>
<body>

<section class="card card--front" aria-label="Business card, front">
  <svg class="card__shape" viewBox="0 0 540 309" aria-hidden="true">
    <path d="M0,0 H540 V64 C450,74 390,120 320,166 C240,214 120,210 0,156 Z" fill="var(--gold)"/>
    <path d="M0,0 H540 V56 C450,66 385,110 315,156 C235,202 118,198 0,146 Z" fill="var(--paper)"/>
  </svg>
  <div class="brand"><span class="brand__dot"></span>Arcadia Oil &amp; Gas</div>
  <div class="social"><span class="social__dot"></span><span class="social__dot"></span></div>
  <div class="person">
    <p class="person__name">Daniel Marsh</p>
    <p class="person__role">President &amp; CEO</p>
  </div>
  <ul class="contact">
    <li class="contact__address">PO Box 48, Harbour Road</li>
    <li class="contact__address">3rd Lane, Leeds</li>
    <li class="contact__row">
      <svg class="contact__icon" viewBox="0 0 14 14" aria-hidden="true"><circle cx="7" cy="7" r="7" fill="var(--gold)"/><path d="M4.5 3.5l1.5 1.5-1 1c.6 1.3 1.5 2.2 2.8 2.8l1-1 1.5 1.5-1 1.2C6.5 10.3 3.7 7.5 3.5 4.5z" fill="var(--ink)"/></svg>
      (123) 555 0187
    </li>
    <li class="contact__row">
      <svg class="contact__icon" viewBox="0 0 14 14" aria-hidden="true"><circle cx="7" cy="7" r="7" fill="var(--gold)"/><rect x="3.5" y="4.5" width="7" height="5" fill="var(--ink)"/><path d="M3.5 4.5l3.5 3 3.5-3" stroke="var(--gold)" stroke-width=".8" fill="none"/></svg>
      hello@arcadiaenergy.com
    </li>
    <li class="contact__row">
      <svg class="contact__icon" viewBox="0 0 14 14" aria-hidden="true"><circle cx="7" cy="7" r="7" fill="var(--gold)"/><circle cx="7" cy="7" r="3.8" fill="none" stroke="var(--ink)" stroke-width="1"/><path d="M3.2 7h7.6M7 3.2v7.6" stroke="var(--ink)" stroke-width=".8"/></svg>
      www.arcadiaenergy.com
    </li>
  </ul>
</section>

<section class="card card--back" aria-label="Business card, back">
  <svg class="card__shape" viewBox="0 0 540 309" aria-hidden="true">
    <path d="M0,110 C70,130 110,190 120,250 C126,285 140,300 160,309 H0 Z" fill="var(--gold)"/>
    <path d="M0,118 C62,138 100,196 110,254 C116,288 128,302 146,309 H0 Z" fill="var(--ink)"/>
    <circle cx="48" cy="262" r="14" fill="var(--paper)"/>
  </svg>
  <div class="brand">Arcadia<span class="brand__sub">Oil &amp; Gas</span></div>
</section>

</body>
</html>
```